Create a memorable Stationary for Security Software Company

Velbrantix is the worldwide leader in securing the Internet. Making Internet communications and critical data secure, reliable and available everywhere has been and continues to be our ongoing vision. We are committed to staying focused on real customer needs and to developing new and innovative security solutions that redefine the security landscape.

Industry/Entity Type

Internet

Font styles to use
Serif
Sans Serif
Script

Colors
0792cd
33a6d7
85cae6

```html
<!DOCTYPE html>
<html lang="en">
<head>
<meta charset="utf-8">
<title>Velbrantix Business Card</title>
<link href="https://fonts.googleapis.com/css2?family=Open+Sans:wght@400;600;700&display=swap" rel="stylesheet">
<style>
  :root {
    --brand-deep: #0792cd;
    --brand-mid: #33a6d7;
    --brand-light: #85cae6;
    --card-dark: #363636;
    --ink-dark: #3a3a3a;
    --ink-light: #f2f2f2;
    --page: #e9ecee;
  }
  html, body {
    margin: 0;
    width: 1200px;
    height: 1120px;
    overflow: hidden;
    background: var(--page);
    font-family: "Open Sans", Arial, sans-serif;
  }
  .sheet {
    position: relative;
    width: 1200px;
    height: 1120px;
  }
  .card {
    position: absolute;
    left: 250px;
    width: 700px;
    height: 400px;
    border-radius: 4px;
    overflow: hidden;
    box-shadow: 0 10px 28px rgba(0,0,0,.22);
  }
  /* Front */
  .card-front {
    top: 70px;
    background: var(--brand-light);
    border-bottom: 6px solid var(--brand-deep);
    box-sizing: border-box;
  }
  .front-brand {
    position: absolute;
    top: 130px;
    left: 0;
    right: 0;
    display: flex;
    justify-content: center;
    align-items: center;
    gap: 16px;
  }
  .brand-dot {
    width: 34px;
    height: 34px;
    border-radius: 50%;
    background: var(--brand-deep);
  }
  .brand-name {
    font-weight: 700;
    font-size: 52px;
    color: var(--brand-deep);
    letter-spacing: 1px;
  }
  .front-web {
    position: absolute;
    bottom: 58px;
    left: 0;
    right: 0;
    text-align: center;
    font-size: 22px;
    letter-spacing: 4px;
    color: var(--ink-dark);
  }
  /* Back */
  .card-back {
    top: 570px;
    background: var(--card-dark);
  }
  .back-brand {
    position: absolute;
    left: 40px;
    top: 135px;
    width: 300px;
    display: flex;
    align-items: center;
    justify-content: center;
    gap: 12px;
  }
  .back-brand .brand-dot { width: 26px; height: 26px; background: var(--brand-mid); }
  .back-brand .brand-name { font-size: 40px; color: var(--brand-mid); }
  .divider {
    position: absolute;
    left: 375px;
    top: 40px;
    width: 2px;
    height: 250px;
    background: linear-gradient(#9a9a9a, #cfcfcf, #7a7a7a);
  }
  .contact {
    position: absolute;
    left: 405px;
    top: 40px;
    color: var(--ink-light);
  }
  .contact-name {
    margin: 0;
    font-size: 22px;
    font-weight: 700;
    color: var(--brand-mid);
  }
  .contact-title {
    margin: 2px 0 22px;
    font-size: 19px;
    font-weight: 600;
  }
  .contact-list {
    list-style: none;
    margin: 0;
    padding: 0;
    font-size: 17px;
  }
  .contact-list li {
    display: flex;
    align-items: flex-start;
    gap: 10px;
    margin-bottom: 5px;
    line-height: 1.3;
  }
  .contact-list li.address { margin-top: 12px; }
  .contact-list svg {
    flex: none;
    width: 15px;
    height: 15px;
    margin-top: 4px;
    fill: var(--brand-mid);
  }
  .wave {
    position: absolute;
    left: 0;
    bottom: 0;
    width: 700px;
    height: 140px;
  }
</style>
</head>
<body>
<main class="sheet">
  <section class="card card-front">
    <div class="front-brand">
      <span class="brand-dot"></span>
      <span class="brand-name">Velbrantix</span>
    </div>
    <p class="front-web">www.velbrantix.com</p>
  </section>

  <section class="card card-back">
    <div class="back-brand">
      <span class="brand-dot"></span>
      <span class="brand-name">Velbrantix</span>
    </div>
    <div class="divider"></div>
    <div class="contact">
      <h2 class="contact-name">Your Name</h2>
      <p class="contact-title">Title</p>
      <ul class="contact-list">
        <li><svg viewBox="0 0 16 16"><path d="M3 1h3l1.5 4-2 1.3a9 9 0 0 0 4.2 4.2L11 8.5l4 1.5v3a2 2 0 0 1-2 2A12 12 0 0 1 1 3a2 2 0 0 1 2-2z"/></svg>012-345-6789</li>
        <li><svg viewBox="0 0 16 16"><path d="M4 0h8a1 1 0 0 1 1 1v14a1 1 0 0 1-1 1H4a1 1 0 0 1-1-1V1a1 1 0 0 1 1-1zm1 2v10h6V2zm3 11a1 1 0 1 0 0 2 1 1 0 0 0 0-2z"/></svg>012-345-6789</li>
        <li><svg viewBox="0 0 16 16"><path d="M0 3h16v10H0zm1.5 1.2L8 9l6.5-4.8V4h-13z"/></svg>info@velbrantix.com</li>
        <li><svg viewBox="0 0 16 16"><path d="M8 0a8 8 0 1 0 0 16A8 8 0 0 0 8 0zm0 1.5c.8 0 1.8 1.7 2.1 4.5H5.9C6.2 3.2 7.2 1.5 8 1.5zM1.6 7h3.2v2H1.6zm4.3 0h4.2v2H5.9zm5.3 0h3.2v2h-3.2zM5.9 10h4.2c-.3 2.8-1.3 4.5-2.1 4.5s-1.8-1.7-2.1-4.5z"/></svg>www.velbrantix.com</li>
        <li class="address"><svg viewBox="0 0 16 16"><path d="M8 0a6 6 0 0 0-6 6c0 4.5 6 10 6 10s6-5.5 6-10a6 6 0 0 0-6-6zm0 8.5A2.5 2.5 0 1 1 8 3.5a2.5 2.5 0 0 1 0 5z"/></svg><span>Street Name, City Name<br>Zipcode-012345</span></li>
      </ul>
    </div>
    <svg class="wave" viewBox="0 0 700 140" preserveAspectRatio="none" aria-hidden="true">
      <path d="M0 70 C120 40 200 110 360 85 S600 20 700 30 V140 H0 Z" fill="var(--brand-mid)"/>
      <path d="M0 88 C130 60 210 125 370 100 S610 40 700 50 V140 H0 Z" fill="var(--card-dark)"/>
      <path d="M0 108 C140 80 230 140 380 118 S620 70 700 80 V140 H0 Z" fill="var(--brand-deep)"/>
    </svg>
  </section>
</main>
</body>
</html>
```